Design a building access mobile app for Quillo by Tamberlin Entry Systems

Hello, We're looking for an awesome designer to create an app design for our app Quillo, by Tamberlin Entry Systems. the mobile app allows employees open their office doors with their mobile phone. this means they don't have to use those plastic card badges or keys. We like clean modern design, dark and light themes. We don't have a logo yet.
Updates

Reason: Waiting on a couple designers to submit concepts

Target Market(s)

Commercial and employees

Industry/Entity Type

Building

Font styles to use
Sans Serif
Other font styles liked:
• Oswald extra light

Requirements
Must have
• nice clean design

```html
<!DOCTYPE html>
<html lang="en">
<head>
<meta charset="utf-8">
<title>Quillo – Profile Settings</title>
<link href="https://fonts.googleapis.com/css2?family=Montserrat:wght@400;500;600&display=swap" rel="stylesheet">
<style>
  :root {
    --page-bg: #e3e7ef;
    --header-bg: #ffffff;
    --ink: #111111;
    --bar-bg: #0f0f10;
    --panel-bg: #161616;
    --field-bg: #2a2a2a;
    --field-text: #f2f2f2;
    --icon-line: #9a9a9a;
    --accent: #1aa3ff;
    --switch-track: #e4e4e4;
    --switch-off: #a9a9a9;
    --avatar-a: #3a3a3c;
    --avatar-b: #8a7a6a;
  }
  * { box-sizing: border-box; margin: 0; padding: 0; }
  html, body {
    width: 800px; height: 1200px; overflow: hidden;
    background: var(--page-bg);
    font-family: "Montserrat", sans-serif;
    color: var(--ink);
  }
  .page { position: relative; width: 800px; height: 1200px; }
  .page-header {
    position: absolute; left: 0; top: 0; width: 800px; height: 64px;
    background: var(--header-bg);
    display: flex; align-items: center; justify-content: space-between;
    padding: 0 18px;
  }
  .project-name { font-size: 24px; font-weight: 500; letter-spacing: 0.5px; }
  .project-meta { font-size: 17px; font-weight: 500; color: #333; letter-spacing: 0.3px; }

  .screen {
    position: absolute; left: 100px; top: 92px; width: 600px; height: 1066px;
    background: #ffffff;
    box-shadow: 0 6px 18px rgba(0,0,0,0.12);
  }
  .top-bar {
    height: 102px; background: var(--bar-bg);
    display: flex; align-items: center; justify-content: space-between;
    padding: 0 22px 0 23px;
  }
  .screen-title {
    color: #fff; font-size: 25px; font-weight: 500; letter-spacing: 0.5px;
  }
  .profile-panel { position: relative; height: 642px; background: var(--panel-bg); }
  .avatar {
    position: absolute; left: 228px; top: 74px; width: 144px; height: 144px;
    border-radius: 50%;
    background: radial-gradient(circle at 50% 40%, var(--avatar-b), var(--avatar-a) 75%);
  }
  .field {
    position: absolute; left: 40px; width: 520px; height: 88px;
    border-radius: 44px; background: var(--field-bg);
    display: flex; align-items: center; padding-left: 36px;
  }
  .field svg { width: 32px; height: 32px; flex: none; }
  .field-value {
    margin-left: 28px; color: var(--field-text); font-size: 19.5px; font-weight: 500;
    letter-spacing: 0.3px;
  }
  .field-name { top: 269px; }
  .field-email { top: 381px; }
  .field-password { top: 493px; }
  .dots { display: flex; gap: 8px; margin-left: 28px; }
  .dots span { width: 8px; height: 8px; border-radius: 50%; background: #fff; }

  .notifications { padding: 50px 51px 0 51px; }
  .section-label {
    color: var(--accent); font-size: 24px; font-weight: 600; letter-spacing: 3px;
  }
  .setting-row {
    display: flex; align-items: center; justify-content: space-between;
    margin-top: 40px; height: 32px;
  }
  .setting-row + .setting-row { margin-top: 40px; }
  .setting-label { font-size: 22px; font-weight: 500; letter-spacing: 1.8px; }
  .switch {
    position: relative; width: 64px; height: 32px; border-radius: 16px;
    background: var(--switch-track);
  }
  .switch::after {
    content: ""; position: absolute; top: 0; width: 32px; height: 32px; border-radius: 50%;
    box-shadow: 0 8px 12px rgba(0,0,0,0.18);
  }
  .switch.is-on::after { right: 0; background: var(--accent); }
  .switch.is-off::after { left: 0; background: var(--switch-off); }
</style>
</head>
<body>
<div class="page">
  <header class="page-header">
    <span class="project-name">Tamberlin Security</span>
    <span class="project-meta">Version 1 / 7 Screens</span>
  </header>

  <main class="screen">
    <div class="top-bar">
      <svg width="34" height="30" viewBox="0 0 34 30" aria-label="Menu">
        <g stroke="#fff" stroke-width="2">
          <line x1="0" y1="2" x2="34" y2="2"/>
          <line x1="0" y1="15" x2="26" y2="15"/>
          <line x1="0" y1="28" x2="34" y2="28"/>
        </g>
      </svg>
      <h1 class="screen-title">PROFILE SETTINGS</h1>
      <svg width="38" height="38" viewBox="0 0 38 38" aria-label="Log out">
        <g fill="none" stroke="#fff" stroke-width="1.8">
          <path d="M12 7 A16 16 0 1 0 26 7"/>
          <line x1="19" y1="1" x2="19" y2="17"/>
        </g>
      </svg>
    </div>

    <section class="profile-panel">
      <div class="avatar" role="img" aria-label="Profile photo of the user"></div>

      <div class="field field-name">
        <svg viewBox="0 0 32 32"><g stroke="var(--icon-line)" stroke-width="1.5"><line x1="0" y1="13" x2="26" y2="13"/><line x1="0" y1="19" x2="32" y2="19"/></g></svg>
        <span class="field-value">John Doe</span>
      </div>

      <div class="field field-email">
        <svg viewBox="0 0 32 32"><g fill="none" stroke="var(--icon-line)" stroke-width="1.5"><rect x="1" y="3" width="30" height="26"/><polyline points="1,4 16,18 31,4"/></g></svg>
        <span class="field-value">jogn.doe.123@mailbox.test</span>
      </div>

      <div class="field field-password">
        <svg viewBox="0 0 32 40" style="height:40px"><g fill="none" stroke="var(--icon-line)" stroke-width="1.5"><path d="M9 13 V9 A7 7 0 0 1 23 9 V13"/><circle cx="16" cy="24" r="15"/><circle cx="16" cy="24" r="3"/></g></svg>
        <div class="dots" aria-label="Password"><span></span><span></span><span></span><span></span><span></span><span></span><span></span><span></span></div>
      </div>
    </section>

    <section class="notifications">
      <h2 class="section-label">NOTIFICATION</h2>
      <div class="setting-row">
        <span class="setting-label">Enable Push Notification</span>
        <span class="switch is-on" aria-label="On"></span>
      </div>
      <div class="setting-row">
        <span class="setting-label">Enable Sound Alert</span>
        <span class="switch is-off" aria-label="Off"></span>
      </div>
    </section>
  </main>
</div>
</body>
</html>
```